Marlow Estate Fixers (Handyman / Home Improvement Company)

Looking for a double sided professional looking business card with Logo attached to be highlighted on one side and throwing in an image of a handyman as an option would be nice to see as well. We are a company focused on providing quality Handyman and Home improvement services in a timely manner that is done right the first time with integrity

Industry/Entity Type

Handyman / Home Improvement

Contact Information for Business Card

(LOGO, Name, Mobile and office phone numbers, email) on front side of card, (the words "The SOLUTION to all of your Handyman and Home Improvement needs" followed by "Family Owned and Operated" at the very bottom) on the back.

Colors
EB3D1F
EC4F4E
F09395
F8D3D4
FCEDEE

Requirements
Must have
• Red, Gray, Black Color scheme
Should not have
• No Yellow or Blue colors

```html
<!DOCTYPE html>
<html lang="en">
<head>
<meta charset="utf-8">
<title>Marlow Estate Fixers — Business Card</title>
<link href="https://fonts.googleapis.com/css2?family=Montserrat:wght@400;500;700;800&display=swap" rel="stylesheet">
<style>
  :root {
    --bg-deep: #111111;
    --bg-mid: #2a2a2a;
    --card: #1e1e1f;
    --card-edge: #2b2b2c;
    --emboss: #2f2f31;
    --red: #eb3d1f;
    --red-soft: #ec4f4e;
    --white: #f4f4f4;
    --muted: #cfcfcf;
  }
  * { box-sizing: border-box; margin: 0; padding: 0; }
  html, body { width: 1200px; height: 875px; overflow: hidden; }
  body {
    background: radial-gradient(ellipse at 60% 40%, var(--bg-mid), var(--bg-deep) 75%);
    font-family: "Montserrat", sans-serif;
    color: var(--white);
    position: relative;
  }
  .card {
    position: absolute;
    top: 282px;
    width: 540px;
    height: 310px;
    border-radius: 18px;
    background: var(--card);
    border: 1px solid var(--card-edge);
    box-shadow: 0 24px 50px rgba(0,0,0,.55);
    overflow: hidden;
  }
  .card--back { left: 40px; }
  .card--front { left: 620px; }

  .brand {
    position: absolute;
    display: flex;
    align-items: center;
    gap: 14px;
    font-weight: 800;
    text-transform: uppercase;
    letter-spacing: 1px;
    line-height: 1.05;
  }
  .brand__dot { flex: none; border-radius: 50%; }
  .card--back .brand {
    left: 50%; top: 50%; transform: translate(-50%, -50%);
    color: var(--emboss); font-size: 34px;
  }
  .card--back .brand__dot { width: 56px; height: 56px; background: var(--emboss); }

  .card--front .brand {
    right: 34px; top: 56px; color: var(--red); font-size: 26px; text-align: left;
  }
  .card--front .brand__dot { width: 44px; height: 44px; background: var(--white); }

  .person { position: absolute; left: 34px; top: 150px; }
  .person__name { font-size: 20px; font-weight: 800; }
  .person__name span { color: var(--red); }
  .person__role { font-size: 11px; font-weight: 400; color: var(--muted); margin-top: 2px; }

  .address { position: absolute; left: 34px; top: 200px; font-size: 11px; line-height: 1.4; color: var(--muted); }

  .contacts { position: absolute; left: 34px; bottom: 22px; list-style: none; font-size: 11px; color: var(--white); }
  .contacts li { display: flex; align-items: center; gap: 8px; line-height: 1.7; }
  .contacts svg { width: 11px; height: 11px; fill: var(--red); flex: none; }
</style>
</head>
<body>
  <section class="card card--back" aria-label="Card back">
    <div class="brand"><span class="brand__dot"></span><span>Marlow Estate<br>Fixers</span></div>
  </section>

  <section class="card card--front" aria-label="Card front">
    <div class="brand"><span class="brand__dot"></span><span>Marlow Estate<br>Fixers</span></div>

    <div class="person">
      <p class="person__name">Dana <span>Whitlock</span></p>
      <p class="person__role">Managing Director</p>
    </div>

    <p class="address">48 Harbor Lane,<br>Fairview, USA</p>

    <ul class="contacts">
      <li><svg viewBox="0 0 24 24"><path d="M6.6 10.8a15 15 0 0 0 6.6 6.6l2.2-2.2c.3-.3.7-.4 1-.2 1.1.4 2.3.6 3.6.6.6 0 1 .4 1 1V20c0 .6-.4 1-1 1A17 17 0 0 1 3 4c0-.6.4-1 1-1h3.5c.6 0 1 .4 1 1 0 1.3.2 2.5.6 3.6.1.3 0 .7-.2 1z"/></svg>(08) 5550 1427</li>
      <li><svg viewBox="0 0 24 24"><path d="M2 5h20v14H2zm2 2v.5l8 5 8-5V7l-8 5z"/></svg>hello@marlowfixers.com</li>
      <li><svg viewBox="0 0 24 24"><circle cx="12" cy="12" r="10"/></svg>www.marlowfixers.com</li>
    </ul>
  </section>
</body>
</html>
```